Web Developer Needs a Business Card Design

I need a personal business card design that represents me as a web developer for potential employers. I would like the background to be a dark color on the front for contrast with my logo and name. The back will have all my information along with a smaller version of the logo. I want something with a modern look and feel, not too conservative. This will be used for potential employers and freelance work.

Industry/Entity Type

Business

Contact Information for Business Card

Front should have my logo and name. The back should have all my personal information which would include: name: Tom Varulek, phone: 570-614-3098, email: tomvarulek@quillbox.net, website url: www.tomvarulek.net, logo, web developer.

Font styles to use
Sans Serif

Requirements
Must have
• Must include my logo. The color palette base color will be the logo color.

```html
<!DOCTYPE html>
<html lang="en">
<head>
<meta charset="utf-8">
<title>Tom Varulek – Business Card</title>
<link href="https://fonts.googleapis.com/css2?family=Lato:wght@400;700&display=swap" rel="stylesheet">
<style>
  :root {
    --stage: #1c1c1c;
    --card: #1c1412;
    --teal: #3db896;
    --teal-deep: #228a70;
    --band: #ffffff;
    --ink: #141414;
    --light: #f2f2f2;
  }
  * { box-sizing: border-box; margin: 0; padding: 0; }
  html, body {
    width: 1200px; height: 1086px; overflow: hidden;
    background: var(--stage);
    font-family: "Lato", sans-serif;
  }
  .card {
    position: absolute; left: 254px; width: 677px; height: 386px;
    background: var(--card); border-radius: 6px; overflow: hidden;
  }
  .card--front { top: 126px; }
  .card--back { top: 587px; }

  .brand { position: absolute; left: 50px; top: 50px; display: flex; align-items: center; }
  .brand__dot {
    width: 96px; height: 96px; border-radius: 50%;
    border: 5px solid var(--teal);
  }
  .brand__name {
    margin-left: 18px; color: var(--teal);
    font-weight: 700; font-size: 42px; letter-spacing: 4px;
  }

  .band {
    position: absolute; left: 0; top: 172px; width: 100%; height: 125px;
    background: var(--band);
  }
  .band__photo {
    position: absolute; left: 0; top: 0; width: 84px; height: 100%;
    background: linear-gradient(90deg, #d6d6d6 0%, #ececec 70%, #ffffff 100%);
  }
  .band__rule {
    position: absolute; left: 52px; top: 52px; width: 492px; height: 2px;
    background: var(--ink);
  }
  .band__name {
    position: absolute; right: 38px; top: 12px;
    color: var(--teal); font-weight: 700; font-size: 29px;
  }
  .band__role {
    position: absolute; right: 38px; top: 50px;
    color: var(--ink); font-size: 22px;
  }

  .contact {
    position: absolute; left: 49px; right: 30px; top: 318px;
    display: flex; align-items: center; gap: 12px;
    color: var(--light); font-size: 18.5px; white-space: nowrap;
  }
  .contact__item { display: flex; align-items: center; gap: 7px; }
  .contact__icon { width: 18px; height: 18px; flex: none; }
  .accent { color: var(--teal); }

  .back-mark {
    position: absolute; left: 249px; top: 102px; width: 184px; height: 184px;
    border-radius: 50%; border: 13px solid var(--teal-deep);
    display: flex; align-items: center; justify-content: center;
  }
  .back-mark__name { color: var(--teal-deep); font-weight: 700; font-size: 22px; letter-spacing: 1px; }
  .back-url {
    position: absolute; left: 0; right: 0; top: 336px; text-align: center;
    color: var(--light); font-size: 21px; letter-spacing: 1px;
  }
  .back-url .accent { color: var(--teal-deep); }
</style>
</head>
<body>
  <section class="card card--front">
    <div class="brand">
      <div class="brand__dot"></div>
      <span class="brand__name">TOM VARULEK</span>
    </div>
    <div class="band">
      <div class="band__photo" role="img" aria-label="Photo of a laptop keyboard seen from above"></div>
      <div class="band__rule"></div>
      <span class="band__name">Tom Varulek</span>
      <span class="band__role">President</span>
    </div>
    <div class="contact">
      <span class="contact__item">
        <svg class="contact__icon" viewBox="0 0 20 20"><path fill="#3db896" d="M2 6c0-2 4-3 8-3s8 1 8 3v2h-4V6.5c-1-.5-3-.7-4-.7s-3 .2-4 .7V8H2zm3 3h10l2 8H3z"/></svg>
        570-614-3098
      </span>
      <span class="contact__item">
        <svg class="contact__icon" viewBox="0 0 20 20"><rect x="1" y="4" width="18" height="12" fill="#3db896"/><path d="M1 4l9 7 9-7M1 16l7-6M19 16l-7-6" stroke="#1c1412" stroke-width="1.4" fill="none"/></svg>
        tomvarulek@quillbox.net
      </span>
      <span class="contact__item">
        <svg class="contact__icon" viewBox="0 0 20 20"><rect x="2" y="4" width="16" height="10" fill="none" stroke="#3db896" stroke-width="2"/><path d="M7 17h6M10 14v3" stroke="#3db896" stroke-width="2"/></svg>
        www.<span class="accent">tomvarulek</span>.net
      </span>
    </div>
  </section>

  <section class="card card--back">
    <div class="back-mark"><span class="back-mark__name">Tom Varulek</span></div>
    <p class="back-url">www.<span class="accent">tomvarulek</span>.net</p>
  </section>
</body>
</html>
```